Launching a new real estate agency in Monaco

Hello, I am opening a new real estate agency in Monaco. For the purpose of my activity, in order to be known quickly among a fierce competition I need an advertising campaign that will be broadcast in local magazines, newspapers, paper board, etc.

You will find example of pictures of Monaco on which I have the rights and my logo. You can always pick other images that I can buy if the price is reasonable for a commercial use (<200 $)

Please respect the color code.

I wish you good luck and look forward to give you my feedbacks

Reason: Only few projects posted were respecting the brief and of quality. Hoping to receive more in coming days

Target Market(s)

International high-end clientele of all ages, all genders.

Industry/Entity Type

Real Estate Agent

Font styles to use
Serif

Requirements
Must have
• 1/ My logo
• 2/ This message "Un nouveau regard sur l'immobilier" means in English a fresh look at real estate or new eyes on real-estate.
• 3/ My address: 14 rue des Ormeaux, Galerie Bellerive Nord, 98 000 Monaco
• 4/ Phone number: +377.93.48.25.07
• 5/ Website: www.corvano-immo.com.
• 6/ Format: Files should be easily adjustable but I'd like a vertical display to fit easily in Magazines, Poster and billboard. So please work in high resolution !
Nice to have
• Please think about your design in accordance with the message I want to display.
Should not have
• A simple poster with a picture of Monaco that does not take into consideration the message of the advertisement, "Un nouveau regard sur l'immobilier" which means in english, new eyes on real-estate or a new look at real-estate, or new vision at real-estate.

```html
<!DOCTYPE html>
<html lang="fr">
<head>
<meta charset="utf-8">
<title>Corvano Immo — Un nouveau regard sur l'immobilier</title>
<link rel="stylesheet" href="https://fonts.googleapis.com/css2?family=Playfair+Display:wght@400&family=Quicksand:wght@500;600&display=swap">
<style>
  :root {
    --slate-dark: #30353f;
    --slate-mid: #474c5a;
    --slate-light: #6a6f7e;
    --copper: #d9987f;
    --white: #ffffff;
    --frame: #24272e;
    --frame-edge: #8d8f96;
    --view-top: #b4b3bf;
    --view-mid: #8f8c74;
    --view-low: #6cbfc8;
  }
  html, body {
    margin: 0;
    padding: 0;
    width: 876px;
    height: 1200px;
    overflow: hidden;
    background: var(--slate-dark);
  }
  .poster {
    position: relative;
    width: 876px;
    height: 1200px;
    overflow: hidden;
    background: radial-gradient(circle at 50% 56%, var(--slate-light) 0%, var(--slate-mid) 38%, var(--slate-dark) 78%);
    color: var(--white);
  }
  .brand {
    position: absolute;
    top: 88px;
    left: 0;
    width: 100%;
    display: flex;
    justify-content: center;
    align-items: center;
    gap: 16px;
    font-family: "Quicksand", sans-serif;
    font-weight: 600;
    font-size: 46px;
    letter-spacing: 6px;
    color: var(--copper);
  }
  .brand-dot {
    width: 26px;
    height: 26px;
    border-radius: 50%;
    background: var(--copper);
  }
  .tagline {
    position: absolute;
    top: 229px;
    left: 0;
    width: 100%;
    margin: 0;
    text-align: center;
    font-family: "Playfair Display", serif;
    font-weight: 400;
    font-size: 32px;
    letter-spacing: 1.8px;
    color: var(--white);
  }
  .scope {
    position: absolute;
    top: 0;
    left: 0;
  }
  .contact {
    position: absolute;
    left: 0;
    width: 100%;
    display: flex;
    justify-content: center;
    align-items: center;
    font-family: "Quicksand", sans-serif;
    font-weight: 500;
    color: var(--white);
  }
  .contact-main {
    top: 1088px;
    font-size: 31px;
    gap: 22px;
  }
  .contact-item {
    display: flex;
    align-items: center;
    gap: 4px;
  }
  .contact-address {
    top: 1143px;
    font-size: 22.5px;
    gap: 4px;
  }
  .icon {
    fill: none;
    stroke: var(--white);
    stroke-width: 1.8;
    stroke-linecap: round;
    stroke-linejoin: round;
  }
</style>
</head>
<body>
<main class="poster">
  <div class="brand"><span class="brand-dot"></span>CORVANO IMMO</div>

  <h1 class="tagline">UN NOUVEAU REGARD SUR L'IMMOBILIER</h1>

  <svg class="scope" width="876" height="1200" viewBox="0 0 876 1200">
    <defs>
      <radialGradient id="glow" cx="50%" cy="50%" r="50%">
        <stop offset="55%" stop-color="#ffffff" stop-opacity="0.10"/>
        <stop offset="82%" stop-color="#e8e4f0" stop-opacity="0.22"/>
        <stop offset="100%" stop-color="#ffffff" stop-opacity="0"/>
      </radialGradient>
      <linearGradient id="view" x1="0" y1="0" x2="0" y2="1">
        <stop offset="0%" stop-color="var(--view-top)"/>
        <stop offset="50%" stop-color="var(--view-mid)"/>
        <stop offset="100%" stop-color="var(--view-low)"/>
      </linearGradient>
    </defs>

    <circle cx="438" cy="690" r="350" fill="url(#glow)" role="img" aria-label="Halo lumineux décoratif autour du viseur"/>

    <circle cx="438" cy="690" r="252" fill="var(--frame)" opacity="0.85"/>
    <circle cx="438" cy="690" r="242" fill="url(#view)" role="img" aria-label="Photo de Monaco : la ville et ses immeubles au pied de la montagne, au bord d'une mer turquoise"/>
    <circle cx="438" cy="690" r="242" fill="none" stroke="var(--frame-edge)" stroke-width="3"/>

    <g stroke="var(--white)" stroke-width="2">
      <line x1="438" y1="313" x2="438" y2="510"/>
      <line x1="438" y1="868" x2="438" y2="1075"/>
      <line x1="55" y1="692" x2="258" y2="692"/>
      <line x1="618" y1="692" x2="820" y2="692"/>
    </g>
  </svg>

  <div class="contact contact-main">
    <span class="contact-item">
      <svg class="icon" width="34" height="34" viewBox="0 0 24 24"><path d="M6.6 3.5l2.6 3.2-1.6 2.2a11 11 0 0 0 7.5 7.5l2.2-1.6 3.2 2.6-1.7 2.6C11.5 20.5 3.5 12.5 4 5.2z"/><path d="M14 4a6 6 0 0 1 6 6"/><path d="M14 7.5a2.5 2.5 0 0 1 2.5 2.5"/></svg>
      +377.93.48.25.07
    </span>
    <span class="contact-item">
      <svg class="icon" width="34" height="34" viewBox="0 0 24 24"><circle cx="12" cy="12" r="9"/><ellipse cx="12" cy="12" rx="4" ry="9"/><line x1="3" y1="12" x2="21" y2="12"/><path d="M4.5 7.5h15M4.5 16.5h15"/></svg>
      www.corvano-immo.com.
    </span>
  </div>

  <div class="contact contact-address">
    <svg class="icon" width="26" height="28" viewBox="0 0 24 24"><path d="M12 21s-6-6.2-6-11a6 6 0 0 1 12 0c0 4.8-6 11-6 11z"/><circle cx="12" cy="10" r="2.3"/><path d="M8 22h8"/></svg>
    14 rue des Ormeaux, Galerie Bellerive Nord, 98 000 Monaco
  </div>
</main>
</body>
</html>
```